Website for BrightlineLabs presentation

We need a new website, ideally as a wordpress there, for BrightlineLabs - we focus on machine learning, big data, data science and data analytics. This website should have two main sections - team presentation, introduction and offered services as static pages, and a blog section.

Target Market(s)

Companies which would like to hire the consultants for data science

Industry/Entity Type

Data Service

Font styles to use
Sans Serif

Colors

Designer to choose colors to be used in the design.

Requirements
Must have
• Wordpress template, blog and presentation pages, nice background images, incorporate the existing logo from brief
Nice to have
• match the word and ppt existing templates for brightline labs

```html
<!DOCTYPE html>
<html lang="en">
<head>
<meta charset="utf-8">
<title>BrightlineLabs</title>
<link href="https://fonts.googleapis.com/css2?family=Lato:wght@400;700;900&family=Oswald:wght@400;500&family=Exo+2:wght@400&display=swap" rel="stylesheet">
<style>
  :root {
    --navy: #12385c;
    --navy-deep: #0c2a48;
    --brand: #1589c7;
    --brand-dark: #0f76ad;
    --pale: #d3e8f4;
    --page: #f2f3f5;
    --ink: #2b2b2b;
    --muted: #666b70;
    --white: #ffffff;
  }
  * { box-sizing: border-box; margin: 0; padding: 0; }
  html, body { width: 1002px; height: 1200px; overflow: hidden; }
  body { position: relative; background: var(--page); font-family: "Lato", sans-serif; color: var(--ink); }

  .hero-bg { position: absolute; inset: 0 0 auto 0; width: 1002px; height: 700px; }

  .site-header { position: absolute; top: 0; left: 0; width: 1002px; height: 100px; }
  .brand { position: absolute; left: 65px; top: 26px; display: flex; align-items: center; gap: 10px; }
  .brand-dot { width: 28px; height: 28px; border-radius: 50%; background: var(--brand); border: 3px solid var(--white); }
  .brand-name { color: var(--white); font-weight: 900; font-size: 19px; line-height: 20px; letter-spacing: .3px; }
  .main-nav { position: absolute; left: 253px; top: 34px; display: flex; color: var(--white); font-size: 15px; }
  .main-nav a { color: inherit; text-decoration: none; }
  .main-nav .sep { margin: 0 22px; }
  .search-btn { position: absolute; left: 696px; top: 26px; width: 35px; height: 35px; border: 1.5px solid var(--white); border-radius: 50%; }
  .phone-pill { position: absolute; left: 766px; top: 26px; width: 171px; height: 34px; border: 1.5px solid var(--white); border-radius: 18px; color: var(--white); font-weight: 700; font-size: 15px; display: flex; align-items: center; gap: 9px; padding-left: 18px; }

  .hero-ring { position: absolute; left: 201px; top: 91px; width: 600px; height: 600px; border-radius: 50%; background: var(--white); }
  .hero-photo { position: absolute; left: 218px; top: 108px; width: 566px; height: 566px; border-radius: 50%;
    background: radial-gradient(circle at 55% 35%, #a8a9a6 0%, #8f9599 40%, #6c7d8c 75%, #55697c 100%); }
  .hero-title { position: absolute; left: 201px; width: 600px; top: 308px; text-align: center; color: var(--white); font-weight: 900; font-size: 44px; line-height: 46px; letter-spacing: 1px; text-shadow: 0 2px 4px rgba(0,0,0,.35); }
  .hero-text { position: absolute; left: 301px; width: 400px; top: 412px; text-align: center; color: var(--white); font-weight: 700; font-size: 13px; line-height: 22px; text-shadow: 0 1px 2px rgba(0,0,0,.4); }
  .btn { position: absolute; display: flex; align-items: center; justify-content: center; background: var(--brand); color: var(--white); font-weight: 700; font-size: 16px; border-radius: 26px; text-decoration: none; }
  .btn-contact { left: 432px; top: 504px; width: 139px; height: 52px; }

  .service { position: absolute; width: 192px; height: 192px; border-radius: 50%; background: var(--white); box-shadow: 0 2px 6px rgba(0,0,0,.12); }
  .service-inner { position: absolute; inset: 9px; border-radius: 50%; background: var(--pale); text-align: center; padding-top: 24px; }
  .service-inner svg { display: block; margin: 0 auto; }
  .service h3 { font-family: "Exo 2", sans-serif; font-weight: 400; font-size: 19px; color: var(--brand); margin-top: 8px; }
  .service p { font-size: 12.5px; line-height: 21px; color: var(--muted); margin-top: 6px; }
  .service.is-featured .service-inner { background: var(--brand); }
  .service.is-featured h3, .service.is-featured p { color: var(--white); }
  .svc-ml { left: 142px; top: 462px; }
  .svc-analytics { left: 633px; top: 462px; }
  .svc-bigdata { left: 291px; top: 581px; }
  .svc-science { left: 483px; top: 581px; }

  .about-title { position: absolute; top: 818px; width: 1002px; text-align: center; font-family: "Oswald", sans-serif; font-weight: 400; font-size: 35px; letter-spacing: -.5px; color: var(--ink); }
  .about-title span { color: var(--brand); font-weight: 500; }
  .about-text { position: absolute; left: 226px; width: 550px; top: 876px; text-align: center; font-size: 13px; line-height: 21.8px; color: var(--muted); }
  .btn-more { left: 432px; top: 992px; width: 139px; height: 52px; }

  .site-footer { position: absolute; left: 0; top: 1096px; width: 1002px; height: 104px; background: var(--brand); color: var(--white); }
  .footer-nav { position: absolute; left: 66px; top: 30px; font-size: 13px; display: flex; }
  .footer-nav a { color: inherit; text-decoration: none; }
  .footer-nav .sep { margin: 0 18px; }
  .copyright { position: absolute; left: 66px; top: 56px; font-size: 13px; }
  .copyright b { font-weight: 700; }
  .social { position: absolute; left: 767px; top: 31px; display: flex; gap: 5px; }
  .social a { width: 39px; height: 39px; border: 1.5px solid var(--white); border-radius: 50%; display: block; }
</style>
</head>
<body>

<svg class="hero-bg" viewBox="0 0 1002 700" aria-hidden="true">
  <defs>
    <linearGradient id="heroShade" x1="0" y1="0" x2="0" y2="1">
      <stop offset="0" stop-color="#0c2a48"/>
      <stop offset="1" stop-color="#1a4d78"/>
    </linearGradient>
  </defs>
  <polygon points="0,0 1002,0 1002,305 501,650 0,305" fill="url(#heroShade)"/>
</svg>

<header class="site-header">
  <div class="brand">
    <span class="brand-dot"></span>
    <span class="brand-name">BRIGHTLINE<br>LABS</span>
  </div>
  <nav class="main-nav">
    <a href="#">Home</a><span class="sep">|</span>
    <a href="#">About</a><span class="sep">|</span>
    <a href="#">Services</a><span class="sep">|</span>
    <a href="#">Blog</a><span class="sep">|</span>
    <a href="#">Contact</a>
  </nav>
  <div class="search-btn">
    <svg width="32" height="32" viewBox="0 0 32 32" aria-label="Search"><circle cx="15" cy="15" r="6.5" fill="none" stroke="#fff" stroke-width="1.6"/><line x1="19.8" y1="19.8" x2="24" y2="24" stroke="#fff" stroke-width="1.8"/></svg>
  </div>
  <div class="phone-pill">
    <svg width="18" height="18" viewBox="0 0 24 24" aria-hidden="true"><path d="M6.6 10.8a15 15 0 0 0 6.6 6.6l2.2-2.2c.3-.3.7-.4 1-.2 1.1.4 2.3.6 3.6.6.6 0 1 .4 1 1V20c0 .6-.4 1-1 1A17 17 0 0 1 3 4c0-.6.4-1 1-1h3.5c.6 0 1 .4 1 1 0 1.2.2 2.4.6 3.6.1.3 0 .7-.2 1z" fill="#fff"/></svg>
    555-014-2290
  </div>
</header>

<div class="hero-ring"></div>
<div class="hero-photo" role="img" aria-label="Photo of a consultant interacting with a digital data interface"></div>
<h1 class="hero-title">BRIGHTLINE<br>LABS</h1>
<p class="hero-text">Lorem Ipsum is simply dummy text of the printing and typesetting industry. Lorem Ipsum has been the industry's standard dummy text ever since the 1500s,</p>
<a class="btn btn-contact" href="#">CONTACT US</a>

<section class="service svc-ml is-featured">
  <div class="service-inner">
    <svg width="44" height="46" viewBox="0 0 44 46" aria-hidden="true" fill="none" stroke="#fff" stroke-width="1.8">
      <rect x="6" y="3" width="32" height="18" rx="4"/><circle cx="19" cy="12" r="4"/><line x1="27" y1="12" x2="32" y2="12"/>
      <path d="M14 21v10h16V21"/><rect x="10" y="34" width="24" height="6"/><line x1="6" y1="43" x2="38" y2="43"/>
    </svg>
    <h3>Machine learning</h3>
    <p>Lorem Ipsum is simply<br>typesetting industry.</p>
  </div>
</section>

<section class="service svc-analytics">
  <div class="service-inner">
    <svg width="48" height="46" viewBox="0 0 48 46" aria-hidden="true" fill="none" stroke="#333" stroke-width="1.8">
      <polyline points="6,18 16,10 26,15 38,5"/><circle cx="6" cy="18" r="2"/><circle cx="16" cy="10" r="2"/><circle cx="26" cy="15" r="2"/><circle cx="38" cy="5" r="2"/>
      <rect x="6" y="28" width="6" height="14"/><rect x="15" y="22" width="6" height="20"/><rect x="24" y="30" width="6" height="12"/><rect x="33" y="20" width="6" height="22"/>
      <line x1="2" y1="43" x2="46" y2="43"/>
    </svg>
    <h3>Data analytics</h3>
    <p>Lorem Ipsum is simply<br>typesetting industry.</p>
  </div>
</section>

<section class="service svc-bigdata">
  <div class="service-inner">
    <svg width="46" height="46" viewBox="0 0 46 46" aria-hidden="true" fill="none" stroke="#333" stroke-width="1.8">
      <path d="M12 18a8 8 0 0 1 10-9 9 9 0 0 1 14 7 6 6 0 0 1-2 11H12a5 5 0 0 1 0-9z"/>
      <rect x="8" y="30" width="9" height="9"/><rect x="19" y="34" width="9" height="9"/><rect x="30" y="30" width="9" height="9"/>
    </svg>
    <h3>Big data</h3>
    <p>Lorem Ipsum is simply<br>typesetting industry.</p>
  </div>
</section>

<section class="service svc-science">
  <div class="service-inner">
    <svg width="46" height="46" viewBox="0 0 46 46" aria-hidden="true" fill="none" stroke="#333" stroke-width="1.8">
      <rect x="12" y="8" width="22" height="30" rx="2"/><circle cx="23" cy="23" r="5"/>
      <line x1="4" y1="14" x2="12" y2="14"/><line x1="4" y1="23" x2="12" y2="23"/><line x1="4" y1="32" x2="12" y2="32"/>
      <line x1="34" y1="14" x2="42" y2="14"/><line x1="34" y1="23" x2="42" y2="23"/><line x1="34" y1="32" x2="42" y2="32"/>
      <line x1="23" y1="2" x2="23" y2="8"/><line x1="23" y1="38" x2="23" y2="44"/>
    </svg>
    <h3>Data science</h3>
    <p>Lorem Ipsum is simply<br>typesetting industry.</p>
  </div>
</section>

<h2 class="about-title">ABOUT <span>BRIGHTLINE LABS</span></h2>
<p class="about-text">Lorem Ipsum is simply dummy text of the printing and typesetting industry. Lorem Ipsum has been the industry's standard dummy text ever since the 1500s, when an unknown printer took a galley of type and scrambled it to make a type specimen book. It has survived not only five centuries, but also the leap into electronic typesetting, remaining essentially unchanged.</p>
<a class="btn btn-more" href="#">READ MORE</a>

<footer class="site-footer">
  <nav class="footer-nav">
    <a href="#">Home</a><span class="sep">|</span>
    <a href="#">About</a><span class="sep">|</span>
    <a href="#">Services</a><span class="sep">|</span>
    <a href="#">Blog</a><span class="sep">|</span>
    <a href="#">Contact</a>
  </nav>
  <p class="copyright">Copyright © <b>BRIGHTLINE LABS</b> - 2018 . All Right Reserved</p>
  <div class="social">
    <a href="#" aria-label="Professional network profile"></a>
    <a href="#" aria-label="Social profile"></a>
    <a href="#" aria-label="Microblog profile"></a>
    <a href="#" aria-label="Community page"></a>
  </div>
</footer>

</body>
</html>
```